German Headhunter/ HR Consultancy needs Business Cards Design

We need a business Card Design for our Company in Stuttgart. We are specialized as Headhunter/ HR Consultancy in Placement of specialist and managers in permanent employment. Please refer to our business logo.

```html
<!DOCTYPE html>
<html lang="de">
<head>
<meta charset="utf-8">
<title>Kernwerk Personalberatung – Visitenkarte</title>
<link href="https://fonts.googleapis.com/css2?family=Questrial&family=Arimo:wght@400&display=swap" rel="stylesheet">
<style>
  :root{
    --stage:#2b2b2d;
    --card:#1e1f22;
    --card-back-dark:#0d0d0e;
    --card-back-light:#3a3a3d;
    --brand-blue:#3d56b2;
    --text-grey:#a9a9ad;
    --rule-grey:#55565a;
  }
  *{margin:0;padding:0;box-sizing:border-box}
  html,body{width:1200px;height:1108px;overflow:hidden;background:var(--stage)}
  .stage{position:relative;width:1200px;height:1108px;display:flex;justify-content:center;align-items:center;gap:80px}
  .card{width:400px;height:618px;border-radius:22px;position:relative;overflow:hidden;box-shadow:0 18px 40px rgba(0,0,0,.45)}
  .card-front{background:var(--card);display:flex;flex-direction:column;align-items:center;padding-top:112px}
  .brand{display:flex;align-items:center;gap:16px}
  .brand-square{width:46px;height:46px;background:var(--brand-blue);border-radius:4px}
  .brand-text{display:flex;flex-direction:column}
  .brand-name{font-family:"Questrial",sans-serif;color:var(--brand-blue);font-size:40px;letter-spacing:1px;line-height:1}
  .brand-sub{font-family:"Questrial",sans-serif;color:var(--text-grey);font-size:15.5px;letter-spacing:1.4px;margin-top:4px}
  .person{margin-top:142px;text-align:center}
  .person-name{font-family:"Questrial",sans-serif;color:var(--brand-blue);font-size:27px;letter-spacing:1px}
  .person-role{font-family:"Questrial",sans-serif;color:var(--text-grey);font-size:15px;letter-spacing:1px;margin-top:2px}
  .icon-row{display:flex;align-items:center;gap:6px;margin-top:14px}
  .icon-row .rule{width:64px;height:1px;background:var(--rule-grey);margin:0 6px}
  .icon-tile{width:30px;height:30px;border-radius:5px;background:var(--brand-blue);display:flex;align-items:center;justify-content:center}
  .contact{font-family:"Arimo",sans-serif;color:var(--text-grey);font-size:17px;line-height:1.5;text-align:center;margin-top:12px}
  .contact .accent{color:var(--brand-blue)}
  .divider{width:212px;height:1px;background:var(--rule-grey);margin-top:12px}
  .address{font-family:"Arimo",sans-serif;color:var(--text-grey);font-size:17px;line-height:1.45;text-align:center;margin-top:12px}
  .card-back{background:var(--card-back-dark)}
  .back-pattern{position:absolute;inset:0;background:linear-gradient(220deg,var(--card-back-light) 0%,#1c1c1e 45%,var(--card-back-dark) 100%)}
  .back-mark{position:absolute;left:50%;top:74%;transform:translate(-50%,-50%);width:48px;height:48px;background:var(--brand-blue);border-radius:4px}
</style>
</head>
<body>
<main class="stage">
  <section class="card card-front" aria-label="Vorderseite">
    <div class="brand">
      <span class="brand-square"></span>
      <div class="brand-text">
        <span class="brand-name">KERNWERK</span>
        <span class="brand-sub">PERSONALBERATUNG</span>
      </div>
    </div>
    <div class="person">
      <p class="person-name">LUKAS BRENNER</p>
      <p class="person-role">MANAGING DIRECTOR</p>
    </div>
    <div class="icon-row">
      <span class="rule"></span>
      <span class="icon-tile" aria-label="Telefon">
        <svg width="18" height="18" viewBox="0 0 24 24"><path fill="#1e1f22" d="M6.6 10.8a15 15 0 0 0 6.6 6.6l2.2-2.2a1 1 0 0 1 1-.25 11 11 0 0 0 3.6.6 1 1 0 0 1 1 1V20a1 1 0 0 1-1 1A17 17 0 0 1 3 4a1 1 0 0 1 1-1h3.5a1 1 0 0 1 1 1 11 11 0 0 0 .6 3.6 1 1 0 0 1-.25 1z"/></svg>
      </span>
      <span class="icon-tile" aria-label="E-Mail">
        <svg width="18" height="18" viewBox="0 0 24 24"><rect x="3" y="6" width="18" height="12" rx="1" fill="none" stroke="#1e1f22" stroke-width="2"/><path d="M3 7l9 6 9-6" fill="none" stroke="#1e1f22" stroke-width="2"/></svg>
      </span>
      <span class="icon-tile" aria-label="Web">
        <svg width="18" height="18" viewBox="0 0 24 24"><circle cx="12" cy="12" r="8" fill="none" stroke="#1e1f22" stroke-width="2"/><path d="M4 12h16M12 4c3 3 3 13 0 16M12 4c-3 3-3 13 0 16" fill="none" stroke="#1e1f22" stroke-width="1.6"/></svg>
      </span>
      <span class="rule"></span>
    </div>
    <p class="contact">
      044-555 018 274<br>
      info@kernwerk-hr.com<br>
      www.<span class="accent">kernwerk-hr</span>.com
    </p>
    <span class="divider"></span>
    <p class="address">421, Address line here<br>45452, Country Name</p>
  </section>

  <section class="card card-back" aria-label="Rückseite">
    <div class="back-pattern" role="img" aria-label="Glanzlack-Muster aus wiederholten Markenzeichen auf schwarzem Grund"></div>
    <span class="back-mark"></span>
  </section>
</main>
</body>
</html>
```